Healthy Meal Delivery Website Needs to be updated, current, fresh and modern

Hi there,

The current website i have is super old and outdated.

I would like a beautiful modern site that has all the same content as the previous except with a a new, modern and trustworthy feel.

The current website is https://tovalplatefresh.com/

Target Market(s)

Health Conscious Young Professionals

Industry/Entity Type

Food Service

Font styles to use
Sans Serif

Requirements
Must have
• Modern Trustworthy feel
Should not have
• Anything out dated or cheesy or scammy

```html
<!DOCTYPE html>
<html lang="en">
<head>
<meta charset="utf-8">
<title>Toval Diet Gourmet — Fresh Diet Meals Delivered</title>
<link href="https://fonts.googleapis.com/css2?family=Lato:wght@400;700;900&family=Open+Sans:wght@400;600&display=swap" rel="stylesheet">
<style>
:root{
  --blue:#1b8fd2;
  --blue-dark:#1479b5;
  --green:#8dc63f;
  --yellow-top:#f8bf16;
  --yellow-bottom:#e9e61c;
  --ink:#1f1f1f;
  --text:#555;
  --white:#fff;
  --footer:#222222;
  --footer-line:#3a3a3a;
  --heading-yellow:#f3d51b;
}
*{margin:0;padding:0;box-sizing:border-box}
html,body{width:1200px;height:3888px;overflow:hidden}
body{font-family:"Open Sans",Arial,sans-serif;color:var(--text);background:var(--white);position:relative}
.abs{position:absolute}
h1,h2,h3,h4,.btn,.nav a,.brand{font-family:"Lato",Arial,sans-serif}

/* header */
.site-header{position:absolute;top:0;left:0;width:1200px;height:90px;background:var(--white)}
.brand{position:absolute;left:118px;top:31px;display:flex;align-items:center;gap:10px;font-weight:900;font-size:22px;color:var(--blue);white-space:nowrap}
.brand-dot{width:28px;height:28px;border-radius:50%;background:var(--green)}
.nav{position:absolute;left:438px;top:37px;display:flex;gap:24px;font-size:15px;white-space:nowrap}
.nav a{color:var(--ink);text-decoration:none}
.nav a.active{color:var(--blue)}
.signup{position:absolute;left:994px;top:30px;width:86px;height:34px;border-radius:17px;background:var(--blue);color:var(--white);font:700 15px "Lato",sans-serif;display:flex;align-items:center;justify-content:center}

/* hero */
.hero{position:absolute;top:90px;left:0;width:1200px;height:547px;background:radial-gradient(ellipse at 55% 55%,#5b6b3a 0%,#3a4227 40%,#262a1f 75%,#1c1d18 100%)}
.hero h1{position:absolute;top:170px;width:100%;text-align:center;color:var(--white);font-weight:900;font-size:44px;letter-spacing:.5px}
.hero p{position:absolute;top:228px;left:300px;width:600px;text-align:center;color:var(--white);font:600 20px/1.45 "Lato",sans-serif}
.btn-ghost-light{position:absolute;left:518px;top:301px;width:166px;height:47px;border:2px solid var(--white);border-radius:24px;color:var(--white);font-weight:700;font-size:16px;display:flex;align-items:center;justify-content:center}
.hero-dots{position:absolute;top:480px;left:548px;display:flex;gap:7px;align-items:center}
.hero-dots span{width:9px;height:9px;border-radius:50%;background:rgba(255,255,255,.55)}
.hero-dots span.on{background:var(--white)}
.hero-dots .arrow{width:20px;height:20px;background:var(--white)}

/* intro */
.intro h2{position:absolute;top:728px;left:200px;width:800px;text-align:center;color:var(--ink);font-weight:900;font-size:28px;line-height:1.35}
.intro p.lead{position:absolute;top:820px;left:250px;width:700px;text-align:center;font-size:14.5px;line-height:1.6}
.plate{position:absolute;left:370px;top:905px;width:460px;height:460px;border-radius:50%;background:radial-gradient(circle,#6a8a3a 0%,#587a2e 45%,#e9ecea 62%,#f4f5f4 100%)}
.feature-icon{position:absolute;width:56px;height:56px;border-radius:50%;background:var(--blue);border:4px solid var(--white);box-shadow:0 0 0 2px #a9d7f0;display:flex;align-items:center;justify-content:center}
.feature{position:absolute;width:200px;font-size:12.5px;line-height:1.45}
.feature h4{font-weight:700;font-size:17px;color:var(--ink);margin-bottom:4px}
.feature.right{text-align:right}

/* yellow band */
.about-band{position:absolute;top:1308px;left:0;width:1200px;height:547px;background:linear-gradient(180deg,var(--yellow-top),var(--yellow-bottom))}
.monitor-screen{position:absolute;left:130px;top:1412px;width:440px;height:282px;border-radius:10px;background:#1b1b1b;padding:14px}
.monitor-screen .shot{width:100%;height:100%;background:linear-gradient(135deg,#c9b79a,#a5744a 50%,#d7cfc0)}
.monitor-chin{position:absolute;left:130px;top:1694px;width:440px;height:36px;background:linear-gradient(#e6e6e6,#cfcfcf);border-radius:0 0 8px 8px}
.monitor-stand{position:absolute;left:300px;top:1730px;width:100px;height:44px;background:linear-gradient(#d6d6d6,#bdbdbd);clip-path:polygon(15% 0,85% 0,100% 100%,0 100%)}
.about-copy{position:absolute;left:628px;top:1390px;width:470px;color:var(--ink)}
.about-copy h2{font-weight:900;font-size:27px;margin-bottom:14px}
.about-copy .tag{font-size:15px;margin-bottom:18px}
.about-copy h5{font:700 13px "Lato",sans-serif;letter-spacing:.3px;margin-bottom:4px}
.about-copy p{font-size:13px;line-height:1.5;margin-bottom:16px}
.btn-ghost-dark{position:absolute;left:629px;top:1709px;width:169px;height:50px;border:2px solid var(--ink);border-radius:25px;color:var(--ink);font-weight:900;font-size:15px;display:flex;align-items:center;justify-content:center}

/* menu */
.menu h2{position:absolute;top:1952px;width:100%;text-align:center;color:var(--blue);font-weight:900;font-size:28px;line-height:1.2}
.dish{position:absolute;top:2046px;width:240px;text-align:center}
.dish-photo{width:223px;height:223px;border-radius:50%;margin:0 auto;border:5px solid var(--ink);box-shadow:inset 0 0 0 4px #e3c21a}
.dish h3{margin-top:26px;font-weight:900;font-size:17px;color:var(--ink)}
.dish p{margin-top:8px;font-size:13px;line-height:1.5}

/* testimonial */
.testimonial-band{position:absolute;top:2430px;left:0;width:1200px;height:515px;background:radial-gradient(ellipse at 50% 50%,#6a6a36 0%,#4a3a26 55%,#2d251c 100%)}
.testimonial-card{position:absolute;left:220px;top:2551px;width:777px;height:267px;border-radius:0 130px 0 130px;background:var(--blue);opacity:.95;color:var(--white);text-align:center}
.testimonial-card h2{margin-top:40px;font-weight:900;font-size:28px}
.testimonial-card blockquote{margin:18px auto 0;width:570px;font-size:19px;line-height:1.45}
.testimonial-card cite{display:block;margin-top:6px;font:900 15px "Lato",sans-serif;font-style:normal;letter-spacing:.5px}
.quote-mark{position:absolute;top:94px;font:900 54px/1 "Lato",sans-serif}

/* real foods */
.ingredients-photo{position:absolute;left:117px;top:3020px;width:432px;height:430px;background:radial-gradient(ellipse at 50% 55%,#c9493a 0%,#d99a33 30%,#8c9e46 50%,#f6f3ee 75%)}
.real-copy{position:absolute;left:575px;top:3080px;width:500px}
.real-copy h2{font-weight:900;font-size:27px;line-height:1.3;color:var(--ink)}
.real-copy p{margin-top:20px;font-size:13.5px;line-height:1.55}
.btn-ghost-blue{position:absolute;left:575px;top:3295px;width:168px;height:47px;border:2px solid var(--blue);border-radius:24px;color:var(--blue);font-weight:700;font-size:15px;display:flex;align-items:center;justify-content:center}

/* footer */
.site-footer{position:absolute;top:3492px;left:0;width:1200px;height:396px;background:var(--footer);color:#e6e6e6}
.site-footer h4{font-weight:900;font-size:22px;color:var(--heading-yellow);margin-bottom:18px}
.foot-about{position:absolute;left:122px;top:72px;width:300px;font-size:13px;line-height:1.6}
.foot-links{position:absolute;left:513px;top:72px;width:300px}
.foot-links ul{list-style:none;columns:2;column-gap:20px;font-size:14px;line-height:2.4}
.foot-social{position:absolute;left:855px;top:72px}
.social-row{display:flex;gap:10px}
.social-row span{width:42px;height:42px;border-radius:50%;border:2px solid #e6e6e6}
.foot-rule{position:absolute;left:122px;top:316px;width:956px;height:1px;background:var(--footer-line)}
.copyright{position:absolute;top:344px;width:100%;text-align:center;font-size:12px;color:#aaa}
</style>
</head>
<body>

<header class="site-header">
  <div class="brand"><span class="brand-dot"></span>Toval Diet Gourmet</div>
  <nav class="nav">
    <a class="active">Home</a><a>Toval Meal Plans</a><a>Menu</a><a>Pricing</a><a>About</a><a>Press</a><a>Contact</a>
  </nav>
  <div class="signup">Sign Up</div>
</header>

<section class="hero" role="img" aria-label="Close-up photo of a fresh salad with greens and tomatoes in a dark bowl">
  <h1>FRESH DIET MEALS DELIVERED</h1>
  <p>Donec convallis pede venenatis nibh Duis quam Nam eget lacus Aliquam erat volutpat Quisque dignissi</p>
  <div class="btn-ghost-light">VIEW MENU</div>
  <div class="hero-dots"><span class="arrow"></span><span class="on"></span><span></span><span></span><span></span><span class="arrow"></span></div>
</section>

<section class="intro">
  <h2>THE TOVAL DIET DELIVERS DIET MEALS TO YOUR DOOR<br>IN TORONTO, GTA AND MONTREAL</h2>
  <p class="lead">Our fresh and delicious diet meals and snacks are made with only the best natural ingredients that nourish your body. Why not let us prepare your meals while you lose the weight?</p>
  <svg class="abs" style="left:290px;top:914px" width="620" height="400" viewBox="0 0 620 400">
    <path d="M20 400 A290 290 0 0 1 600 400" fill="none" stroke="#a9d7f0" stroke-width="3"/>
  </svg>
  <div class="plate" role="img" aria-label="Photo of a salad with greens, tomatoes and sliced chicken on a white plate"></div>

  <div class="feature-icon" style="left:382px;top:944px"><svg width="26" height="26" viewBox="0 0 24 24"><path d="M12 21s-8-5-8-11a4.5 4.5 0 0 1 8-2.8A4.5 4.5 0 0 1 20 10c0 6-8 11-8 11z" fill="none" stroke="#fff" stroke-width="2"/></svg></div>
  <div class="feature-icon" style="left:754px;top:944px"><svg width="26" height="26" viewBox="0 0 24 24"><path d="M5 19C5 9 11 5 20 4c-1 9-5 15-15 15zM5 19l8-8" fill="none" stroke="#fff" stroke-width="2"/></svg></div>
  <div class="feature-icon" style="left:278px;top:1099px"><svg width="26" height="26" viewBox="0 0 24 24"><circle cx="12" cy="12" r="9" fill="none" stroke="#fff" stroke-width="2"/><path d="M7.5 12l3 3 6-6" fill="none" stroke="#fff" stroke-width="2"/></svg></div>
  <div class="feature-icon" style="left:852px;top:1099px"><svg width="26" height="26" viewBox="0 0 24 24"><circle cx="12" cy="12" r="4" fill="none" stroke="#fff" stroke-width="2.5"/><path d="M12 2v4M12 18v4M2 12h4M18 12h4M5 5l3 3M16 16l3 3M5 19l3-3M16 8l3-3" stroke="#fff" stroke-width="2.5"/></svg></div>

  <div class="feature right" style="left:164px;top:936px"><h4>Healthy</h4>The Toval Diet is a great way to ensure you are eating all the nutrients you need, and</div>
  <div class="feature" style="left:829px;top:936px"><h4>Fresh</h4>The Toval Diet is a great way to ensure you are eating all the nutrients you need, and</div>
  <div class="feature right" style="left:60px;top:1092px"><h4>Choice</h4>You can choose your own meals from over 100 tasty entrees, desserts and snack</div>
  <div class="feature" style="left:925px;top:1092px"><h4>Customized</h4>You can choose your own meals from over 100 tasty entrees, desserts and snack</div>
</section>

<section class="about-band">
</section>
<div class="monitor-screen"><div class="shot" role="img" aria-label="Photo of a papaya salad with peanuts and herbs shown on a desktop screen"></div></div>
<div class="monitor-chin"></div>
<div class="monitor-stand"></div>
<div class="about-copy">
  <h2>THE TOVAL DIET</h2>
  <p class="tag">Real foods designed by nature prepared by Toval.</p>
  <h5>WHAT YOU GET</h5>
  <p>Toval Diet Delivery provides you with 3 fresh daily meals and 3 snacks delivered to your doorstep before 8am.</p>
  <h5>SELECTION</h5>
  <p>Choose your meals from over 100 delicious entrees, snacks and desserts</p>
  <h5>LUXURY</h5>
  <p>Enjoy the luxury of having your own personal chef and nutritionist prepare Toval Diet meals for you.</p>
</div>
<div class="btn-ghost-dark">READ MORE</div>

<section class="menu">
  <h2>SELECT FROM<br>OVER 100 MENU ITEMS</h2>
  <div class="dish" style="left:103px"><div class="dish-photo" role="img" aria-label="Photo of a colourful grain bowl with vegetables" style="background:radial-gradient(circle,#7a9a3a,#b5562e 55%,#4c6b2a)"></div><h3>MENU TITLE</h3><p>Morbi diam mauris viverra in gravida eu mattis in ante</p></div>
  <div class="dish" style="left:354px"><div class="dish-photo" role="img" aria-label="Photo of golden waffles" style="background:radial-gradient(circle,#c88a3e,#9a5a22 60%,#5a3a1a)"></div><h3>MENU TITLE</h3><p>Morbi diam mauris viverra in gravida eu mattis in ante</p></div>
  <div class="dish" style="left:605px"><div class="dish-photo" role="img" aria-label="Photo of grilled fish with vegetables" style="background:radial-gradient(circle,#d9b58a,#9c6a3e 55%,#4a4a3a)"></div><h3>MENU TITLE</h3><p>Morbi diam mauris viverra in gravida eu mattis in ante</p></div>
  <div class="dish" style="left:854px"><div class="dish-photo" role="img" aria-label="Photo of a fresh tomato and greens salad" style="background:radial-gradient(circle,#d2463a,#8fb04a 55%,#e8e2d6)"></div><h3>MENU TITLE</h3><p>Morbi diam mauris viverra in gravida eu mattis in ante</p></div>
</section>

<section class="testimonial-band" role="img" aria-label="Photo of a grilled chicken and vegetable salad on a plate over burlap"></section>
<div class="testimonial-card">
  <h2>TESTIMONIALS</h2>
  <span class="quote-mark" style="left:82px">“</span>
  <span class="quote-mark" style="right:82px">”</span>
  <blockquote>I have been very impressed with the food. I've done a few other meal delivery services and yours is by far the best in terms of flavour, freshness and quality. "<cite>MARLA</cite></blockquote>
</div>

<section class="real-foods">
  <div class="ingredients-photo" role="img" aria-label="Photo of fresh peppers, tomatoes, olive oil, grains and a wooden bowl"></div>
  <div class="real-copy">
    <h2>THE TOVAL DIET IS BASED ON<br>REAL FOODS MADE WITH FRESH AND<br>NATURAL INGREDIENTS</h2>
    <p>t's about eating the foods you love and emphasizing the ones that nourish your body: generous portions of fresh fruit, vegetables, meat, fish, nuts and seeds, with smaller servings of grains and dairy.a</p>
  </div>
  <div class="btn-ghost-blue">READ MORE</div>
</section>

<footer class="site-footer">
  <div class="foot-about">
    <h4>WHAT IS TOVAL?</h4>
    Toval is the Toronto &amp; Montreal Diet Delivery program based on the Toval Diet™, healthy carbs and the right fats. We provide you with 3 fresh meals, 2 snacks and a dessert delivered to your door before 8am. Try our Toval Diet™ delivery plan and start Toval weight loss now!
  </div>
  <div class="foot-links">
    <h4>QUICK LINKS</h4>
    <ul><li>Home</li><li>Toval Meal Plans</li><li>Menu</li><li>Pricing</li><li>About</li><li>Press</li><li>Contact</li></ul>
  </div>
  <div class="foot-social">
    <h4>GET IN TOUCH</h4>
    <div class="social-row"><span aria-label="Social link"></span><span aria-label="Social link"></span><span aria-label="Social link"></span><span aria-label="Social link"></span></div>
  </div>
  <div class="foot-rule"></div>
  <p class="copyright">© 2018 Company Name. All right reserved. Terms of Use</p>
</footer>

</body>
</html>
```